Business Cards for IT Consulting Company (Managed Service Provider)

I am looking to have some business cards printed and would like some designs. We are an IT Consulting company based in Vancouver BC. I would like a nice clean and modern look to the cards. I have uploaded all the versions of my logo so parts can be used as needed. Here is a snippit from our website homepage:

Quillbrook Networks Ltd. is an IT Solutions Partner located in Vancouver BC, Canada. We offer IT solutions and support to customers in the greater Vancouver Area. With expertise in Microsoft platforms, as well as Linux and Mac OSX and over 12 years experience in the IT industry, Quillbrook Networks is dedicated to offering our clients top quality service and products. We take pride in the solutions we offer our customers. The greatest compliment a client can give us is to recommend our services.

Quillbrook Networks Ltd. offers a wide range of IT services from onsite service to remote support and managed service solutions. This allows clients to choose the support path that best suits their company’s needs. Supporting many different sized companies from small to enterprise level over the past 12 years Quillbrook Networks has the experience and expertise needed to ensure things run smoothly. Allowing our clients to focus on doing business.

Revolutionizing the way IT services are delivered.

Quillbrook Networks is dedicated to providing our clients with IT solutions that work and grow with them for years to come. This philosophy helps save money in the long run instead of replacing equipment constantly. Far too often IT solutions are not well thought out and while possibly solving the problem at hand, require replacement due to growth or quality within a very short time frame. Quillbrook Networks takes pride in providing solutions that will last and be able to accommodate growth without the need for replacement.

Industry/Entity Type

Information Technology

Contact Information for Business Card

Quillbrook Networks Ltd.
(Employee Name)
Eml: (Employees Email Address)
Web: quillbrook.me
Ph: 604-555-0148

Font styles to use
Serif
Sans Serif

Requirements
Must have
• The Company logo and company colors.
Nice to have
• - Our tag line: "Revolutionizing IT Services" or "Revolutionizing the way IT services are delivered."
• - Also I really like the idea of nature and technology together blending which is sort of where my logo came from so integrating that somehow onto the business cards would be great.

```html
<!DOCTYPE html>
<html lang="en">
<head>
<meta charset="utf-8">
<title>Quillbrook Networks Ltd. – Business Cards</title>
<link rel="stylesheet" href="https://fonts.googleapis.com/css2?family=Montserrat:wght@500;600;700&display=swap">
<style>
  :root {
    --stage: #2a2a2a;
    --card-black: #050505;
    --brand-blue: #1aa3e8;
    --white: #ffffff;
    --soft-grey: #cfcfcf;
  }
  * { margin: 0; padding: 0; box-sizing: border-box; }
  html, body {
    width: 1200px; height: 900px; overflow: hidden;
    background: var(--stage);
    font-family: "Montserrat", Arial, sans-serif;
  }
  .canvas { position: relative; width: 1200px; height: 900px; }

  .card {
    position: absolute;
    width: 600px; height: 344px;
    border-radius: 22px;
    background: var(--card-black);
    overflow: hidden;
    box-shadow: 0 14px 30px rgba(0,0,0,.45);
  }
  .card--front { left: 90px; top: 110px; }
  .card--back  { left: 510px; top: 446px; }

  /* Front */
  .front-brand {
    position: absolute; left: 0; right: 0; top: 150px;
    display: flex; align-items: center; justify-content: center; gap: 14px;
    color: var(--brand-blue); font-weight: 600; font-size: 30px; letter-spacing: .5px;
  }
  .brand-square {
    width: 30px; height: 30px; border: 3px solid var(--brand-blue);
  }

  /* Back */
  .back-brand {
    position: absolute; left: 40px; top: 108px; width: 210px;
    display: flex; align-items: center; gap: 12px;
    color: var(--brand-blue); font-weight: 600; font-size: 22px; line-height: 1.2;
  }
  .back-brand .brand-square { flex: none; width: 34px; height: 34px; }
  .divider {
    position: absolute; left: 270px; top: 70px; width: 2px; height: 150px;
    background: linear-gradient(180deg, transparent, #bdbdbd 50%, transparent);
  }
  .contact { position: absolute; left: 296px; top: 78px; color: var(--white); }
  .contact__name {
    color: var(--brand-blue); font-weight: 700; font-size: 24px; letter-spacing: 2px;
  }
  .contact__role { font-weight: 500; font-size: 14px; letter-spacing: 1px; margin: 2px 0 14px; }
  .contact__line {
    display: flex; align-items: center; gap: 10px;
    font-weight: 500; font-size: 15px; letter-spacing: .5px; margin-bottom: 7px;
  }
  .contact__line svg { width: 13px; height: 13px; flex: none; }

  .tag-band {
    position: absolute; left: 0; right: 0; bottom: 0; height: 64px;
    background: var(--white);
    border-top: 5px solid var(--brand-blue);
    display: flex; align-items: center; justify-content: center;
    color: var(--brand-blue); font-weight: 600; font-size: 20px; letter-spacing: 1px;
  }
</style>
</head>
<body>
<main class="canvas">
  <section class="card card--front" aria-label="Card front">
    <div class="front-brand">
      <span class="brand-square"></span>
      <span>Quillbrook Networks Ltd.</span>
    </div>
  </section>

  <section class="card card--back" aria-label="Card back">
    <div class="back-brand">
      <span class="brand-square"></span>
      <span>Quillbrook Networks</span>
    </div>
    <div class="divider"></div>
    <div class="contact">
      <p class="contact__name">MARCUS HALE</p>
      <p class="contact__role">DIRECTOR</p>
      <p class="contact__line">
        <svg viewBox="0 0 24 24" fill="#1aa3e8" aria-hidden="true"><path d="M6.6 10.8a15.1 15.1 0 0 0 6.6 6.6l2.2-2.2a1 1 0 0 1 1-.25 11.4 11.4 0 0 0 3.6.57 1 1 0 0 1 1 1V20a1 1 0 0 1-1 1A17 17 0 0 1 3 4a1 1 0 0 1 1-1h3.5a1 1 0 0 1 1 1c0 1.25.2 2.45.57 3.57a1 1 0 0 1-.25 1z"/></svg>
        604-555-0148
      </p>
      <p class="contact__line">
        <svg viewBox="0 0 24 24" fill="none" stroke="#1aa3e8" stroke-width="2.2" aria-hidden="true"><rect x="3" y="5" width="18" height="14" rx="1"/><path d="M3 6l9 7 9-7"/></svg>
        info@marcushale.com
      </p>
      <p class="contact__line">
        <svg viewBox="0 0 24 24" fill="none" stroke="#1aa3e8" stroke-width="2" aria-hidden="true"><circle cx="12" cy="12" r="9"/><path d="M3 12h18M12 3c3 3 3 15 0 18M12 3c-3 3-3 15 0 18"/></svg>
        www.quillbrook.me
      </p>
    </div>
    <div class="tag-band">Revolutionizing IT Services</div>
  </section>
</main>
</body>
</html>
```